KRT Info Brochure

We need a brochure design for a new not-for-profit organisation that is aimed at providing homeless people with a residence that also provides counselling and vocational training to assist them to find suitable employment at the end of the program.
PLEASE NOTE:
Brochure to be A4.
I know the brochure is quite long, it is really a booklet, but please note that it does not have to have a lot of work done on it, I just want it to look professional and the front cover and inside page to look good.
Also please leave about 2-3 pages at the end as I will be adding in some architect drawings.
Please add in a last page with Contact written at the bottom - we will fill that in later. So please ensure it is editable in PDF.
Thank you so much.
Cheers
Marta

```html
<!DOCTYPE html>
<html lang="en">
<head>
<meta charset="utf-8">
<title>KRT Legacy Foundation – Brochure Cover</title>
<link href="https://fonts.googleapis.com/css2?family=Arimo:wght@400;700&family=Tinos:wght@700&display=swap" rel="stylesheet">
<style>
  :root {
    --stage: #e4e4e4;
    --olive-light: #8f8c3a;
    --olive: #7d7a2c;
    --olive-dark: #65621f;
    --orange: #f2a81d;
    --orange-deep: #e8901a;
    --white: #ffffff;
    --photo-warm: #c9a45a;
    --photo-stone: #a88a52;
    --photo-shadow: #6d5a3a;
  }
  * { margin: 0; padding: 0; box-sizing: border-box; }
  html, body {
    width: 1200px; height: 847px; overflow: hidden;
    background: radial-gradient(ellipse at 50% 20%, #f6f6f6 0%, var(--stage) 70%);
    font-family: "Arimo", Arial, sans-serif;
  }
  .spread {
    position: absolute; left: 105px; top: 74px;
    width: 990px; height: 700px; display: flex;
    box-shadow: 0 18px 40px rgba(0,0,0,.25);
  }
  .page { position: relative; width: 495px; height: 700px; overflow: hidden; }

  /* Back cover */
  .back-cover {
    background: radial-gradient(ellipse at 40% 40%, var(--olive-light) 0%, var(--olive) 55%, var(--olive-dark) 100%);
  }
  .back-cover__mark {
    position: absolute; left: 40px; top: 150px;
    width: 380px; height: 380px; border-radius: 50%;
    background: rgba(255,255,255,.07);
  }
  .back-cover__mark-name {
    position: absolute; left: 40px; top: 290px; width: 380px;
    text-align: center; font-family: "Tinos", serif; font-weight: 700;
    font-size: 96px; color: rgba(255,255,255,.1);
  }

  /* Shared contact block */
  .contact {
    position: absolute; right: 40px; color: var(--white);
    font-size: 13px; line-height: 1.35; text-align: right;
  }
  .contact strong { font-weight: 700; }
  .back-cover .contact { bottom: 60px; }

  /* Front cover */
  .front-cover { background: var(--white); }
  .front-cover__art { position: absolute; inset: 0; }
  .brand {
    position: absolute; left: 0; right: 0; top: 34px;
    display: flex; align-items: center; justify-content: center; gap: 10px;
  }
  .brand__dot { width: 34px; height: 34px; border-radius: 50%; background: var(--orange); }
  .brand__name {
    font-family: "Arimo", Arial, sans-serif; font-weight: 700;
    font-size: 22px; color: var(--orange-deep); letter-spacing: .5px;
  }
  .title {
    position: absolute; left: 0; right: 0; top: 420px; text-align: center;
    font-family: "Tinos", "Times New Roman", serif; font-weight: 700;
    color: var(--white); text-transform: uppercase; line-height: 1.1;
  }
  .title__main { display: block; font-size: 34px; }
  .title__sub { display: block; font-size: 28px; letter-spacing: .5px; }
  .front-cover .contact { top: 520px; right: 60px; }
</style>
</head>
<body>
  <main class="spread">
    <section class="page back-cover">
      <div class="back-cover__mark" aria-hidden="true"></div>
      <div class="back-cover__mark-name" aria-hidden="true">KRT</div>
      <address class="contact">
        Contact Us : <strong>555-204-7719</strong><br>
        info@KRTfoundation.org &nbsp;|&nbsp; www.KRTfoundation.org
      </address>
    </section>

    <section class="page front-cover">
      <svg class="front-cover__art" width="495" height="700" viewBox="0 0 495 700">
        <defs>
          <linearGradient id="photoTone" x1="0" y1="0" x2="1" y2="1">
            <stop offset="0" stop-color="var(--photo-warm)"/>
            <stop offset=".55" stop-color="var(--photo-stone)"/>
            <stop offset="1" stop-color="var(--photo-shadow)"/>
          </linearGradient>
          <radialGradient id="oliveTone" cx=".5" cy=".4" r=".8">
            <stop offset="0" stop-color="var(--olive-light)"/>
            <stop offset="1" stop-color="var(--olive-dark)"/>
          </radialGradient>
        </defs>
        <rect class="cover-olive" x="0" y="290" width="495" height="410" fill="url(#oliveTone)"/>
        <path class="cover-orange-wave" d="M0 345 Q200 300 495 270 L495 330 Q250 330 0 385 Z" fill="var(--orange)"/>
        <path class="cover-white-line" d="M0 360 Q220 318 495 290 L495 298 Q230 325 0 368 Z" fill="var(--white)"/>
        <path class="cover-photo" role="img" aria-label="Photograph: an elderly man in a cap sitting against a sandstone wall beside a barred window"
              d="M0 95 Q240 75 495 120 L495 270 Q200 300 0 345 Z" fill="url(#photoTone)"/>
      </svg>

      <div class="brand">
        <span class="brand__dot" aria-hidden="true"></span>
        <span class="brand__name">KRT Legacy Foundation</span>
      </div>

      <h1 class="title">
        <span class="title__main">KRT</span>
        <span class="title__sub">Legacy Foundation</span>
      </h1>

      <address class="contact">
        Contact Us : <strong>555-204-7719</strong><br>
        info@KRTfoundation.org &nbsp;|&nbsp; www.KRTfoundation.org
      </address>
    </section>
  </main>
</body>
</html>
```